New Business Card Design Project

Need a design that will create an impact / strong impression towards our clients for our business. We are in the lighting business and we do lighting retrofits for large commercial to industrial clientele.

Target Market(s)

Lighting Industry

Industry/Entity Type

Business

Font styles to use
Other font styles liked:
• we would like to use the font on our logo, not sure what it is though..

Requirements
Must have
• Our logo.
Nice to have
• We are open to suggestions that have to do with lighting.

```html
<!DOCTYPE html>
<html lang="en">
<head>
<meta charset="utf-8">
<title>Brightline Retrofit Partners – Business Card</title>
<link href="https://fonts.googleapis.com/css2?family=Lato:wght@400;700;900&display=swap" rel="stylesheet">
<style>
  :root {
    --backdrop: #3b3b3d;
    --forest: #143a12;
    --green: #0c8038;
    --leaf: #5cc457;
    --ink: #1b1b1b;
    --paper: #ffffff;
  }
  html, body {
    margin: 0;
    width: 1200px;
    height: 900px;
    overflow: hidden;
    background: var(--backdrop);
    font-family: 'Lato', sans-serif;
  }
  .card {
    position: absolute;
    left: 260px;
    width: 680px;
    height: 388px;
    overflow: hidden;
    box-shadow: 0 6px 18px rgba(0,0,0,.45);
  }
  .card--back { top: 44px; background: var(--forest); }
  .card--front { top: 468px; background: var(--paper); }

  .brand {
    display: flex;
    align-items: center;
    gap: 12px;
    font-weight: 900;
    letter-spacing: .5px;
    margin: 0;
  }
  .brand__square { width: 22px; height: 22px; display: block; }
  .card--back .brand {
    position: absolute; left: 0; right: 0; top: 140px;
    justify-content: center;
    font-size: 46px; color: var(--paper);
  }
  .card--back .brand__square { background: var(--leaf); }
  .card--back .web {
    position: absolute; left: 0; right: 0; bottom: 58px; margin: 0;
    text-align: center; color: var(--paper);
    font-size: 17px; letter-spacing: 1.5px;
  }

  .card--front .brand {
    position: absolute; left: 40px; top: 48px;
    font-size: 38px; color: var(--forest);
  }
  .card--front .brand__square { background: var(--green); }
  .divider {
    position: absolute; left: 40px; right: 40px; top: 180px;
    height: 2px; background: var(--green);
  }
  .contact {
    position: absolute; left: 40px; top: 208px;
    list-style: none; margin: 0; padding: 0;
    font-size: 18px; color: var(--ink); line-height: 27px;
  }
  .contact li { display: flex; align-items: center; gap: 12px; }
  .contact svg { width: 16px; height: 16px; fill: var(--green); }
  .person {
    position: absolute; right: 40px; top: 196px; text-align: right;
  }
  .person__name {
    margin: 0; font-size: 30px; font-weight: 700; color: var(--green);
    border-bottom: 2px solid var(--green); padding-bottom: 2px;
  }
  .person__role { margin: 2px 0 0; font-size: 18px; color: var(--ink); }
  .person__address {
    margin: 14px 0 0; font-size: 18px; color: var(--ink);
    font-style: normal; line-height: 24px;
  }
  .footer-band { position: absolute; left: 0; bottom: 0; width: 680px; height: 64px; display: block; }
  .footer-web {
    position: absolute; right: 40px; bottom: 12px; margin: 0;
    font-size: 17px; line-height: 20px; color: var(--paper); letter-spacing: .5px;
    white-space: nowrap;
  }
</style>
</head>
<body>

<section class="card card--back">
  <h1 class="brand"><span class="brand__square"></span>Brightline Retrofit</h1>
  <p class="web">www.brightline-retro.com</p>
</section>

<section class="card card--front">
  <h1 class="brand"><span class="brand__square"></span>Brightline Retrofit</h1>
  <div class="divider"></div>

  <ul class="contact">
    <li>
      <svg viewBox="0 0 16 16" aria-hidden="true"><path d="M3.5 1l2.5 3-1.5 1.8c.9 2 2.4 3.5 4.3 4.4L10.6 8.7l3.2 2.3-1 3c-6.2.4-11-4.6-10.8-10.8z"/></svg>
      (555) 214-3300
    </li>
    <li>
      <svg viewBox="0 0 16 16" aria-hidden="true"><path d="M4 1h8v4H4zM1 6h14v6h-3v3H4v-3H1zM5 10v4h6v-4z"/></svg>
      (555) 214-3301
    </li>
    <li>
      <svg viewBox="0 0 16 16" aria-hidden="true"><path d="M1 3h14v10H1zM2 4.2v.4l6 4 6-4v-.4z" fill-rule="evenodd"/></svg>
      hello@brightline-retro.com
    </li>
  </ul>

  <div class="person">
    <h2 class="person__name">Daniel Mercer</h2>
    <p class="person__role">Manager</p>
    <address class="person__address">1480 North Maple Avenue<br>Fairview, IL 60400</address>
  </div>

  <svg class="footer-band" viewBox="0 0 680 64" aria-hidden="true">
    <rect x="0" y="34" width="680" height="30" fill="var(--green)"/>
    <path d="M352 64 Q376 12 420 12 H680 V64 Z" fill="var(--paper)"/>
    <path d="M362 64 Q386 18 426 18 H680 V64 Z" fill="var(--forest)"/>
  </svg>
  <p class="footer-web">www.brightline-retro.com</p>
</section>

</body>
</html>
```